Business card design for Automotive workshop

We need a business card for a new automotive repair and tyre shop called Keelstone Prime Automotive located in New Zealand. We are a clean, modern and fresh workshop and company.

Front needs to feature logo,
my name:
Marlo Fenwicke (director)

Address:
48 Tarn Lane
Whitianga 3510

Phone: 07 594 2713
Mobile: 027 451 9362
Email: office@keelstoneautomotive.example.nz
Website: keelstoneautomotive.example.nz

Back needs to feature an area to write down appointment details, date and time.

Also feature a list of jobs and work we do such as,
Vehicle Servicing
All Mechanical Repairs
Warrant of Fitness
Tyres & Wheel Alignments
Automotive Diagnostics
Automotive Parts & Supplies

```html
<!DOCTYPE html>
<html lang="en">
<head>
<meta charset="utf-8">
<title>Keelstone Prime Automotive – Business Card</title>
<link rel="stylesheet" href="https://fonts.googleapis.com/css2?family=Open+Sans:wght@400;700;800&display=swap">
<style>
  :root {
    --stage-center: #555555;
    --stage-edge: #1f1f1f;
    --card-white: #ffffff;
    --panel-dark: #2d2d2d;
    --brand-red: #e0242b;
    --ink: #1a1a1a;
    --font: "Open Sans", Arial, sans-serif;
  }
  * { box-sizing: border-box; margin: 0; padding: 0; }
  html, body { width: 1200px; height: 750px; overflow: hidden; }
  body {
    position: relative;
    font-family: var(--font);
    color: var(--ink);
    background: radial-gradient(ellipse at 50% 50%, var(--stage-center) 0%, #3a3a3a 45%, var(--stage-edge) 100%);
  }
  .card {
    position: absolute;
    background: var(--card-white);
    box-shadow: 0 3px 8px rgba(0,0,0,.45);
    overflow: hidden;
  }
  .card--front { left: 38px; top: 186px; width: 559px; height: 328px; }
  .card--back  { left: 610px; top: 187px; width: 562px; height: 328px; }

  .brand-panel { position: absolute; background: var(--panel-dark); display: flex; align-items: center; justify-content: center; }
  .card--front .brand-panel { left: 18px; top: 0; width: 245px; height: 328px; }
  .card--back .brand-panel { left: 221px; top: 0; width: 341px; height: 269px; }

  .brand-name {
    color: var(--brand-red);
    font-weight: 800;
    text-transform: uppercase;
    text-align: center;
    line-height: 1.1;
    letter-spacing: .5px;
  }
  .card--front .brand-name { font-size: 21px; }
  .card--back .brand-name { font-size: 28px; }

  .contact { position: absolute; left: 0; top: 0; width: 100%; height: 100%; }
  .person { position: absolute; left: 276px; top: 72px; display: flex; align-items: center; gap: 6px; height: 24px; }
  .person svg { width: 11px; height: 12px; flex: none; }
  .person-name { font-weight: 700; font-size: 18px; line-height: 24px; white-space: nowrap; }
  .person-title { position: absolute; left: 293px; top: 92px; font-size: 13.5px; line-height: 18px; }
  .address { position: absolute; left: 270px; top: 128px; font-size: 15px; line-height: 22px; white-space: nowrap; }

  .contact-row { position: absolute; left: 268px; display: flex; align-items: center; gap: 5px; font-size: 13.5px; line-height: 20px; height: 20px; white-space: nowrap; }
  .contact-row svg { width: 12px; height: 12px; flex: none; }
  .row-mobile { top: 169px; }
  .row-phone  { top: 192px; }
  .row-email  { top: 214px; }
  .row-web    { top: 238px; }

  .services { list-style: none; position: absolute; left: 0; top: 0; }
  .service { position: absolute; left: 0; display: flex; align-items: center; font-size: 14.5px; white-space: nowrap; letter-spacing: .2px; }
  .service svg { width: 13px; height: 24px; margin-right: 7px; flex: none; }

  .appointment { position: absolute; top: 285px; left: 279px; display: flex; gap: 6px; font-size: 16px; }
  .appointment-field { display: flex; align-items: flex-end; }
  .blank { display: inline-block; width: 86px; border-bottom: 1px solid var(--ink); margin-bottom: 4px; margin-left: 1px; }
</style>
</head>
<body>

<section class="card card--front" aria-label="Business card front">
  <div class="brand-panel">
    <p class="brand-name">Keelstone Prime<br>Automotive</p>
  </div>
  <div class="contact">
    <div class="person">
      <svg viewBox="0 0 12 12" aria-hidden="true"><circle cx="6" cy="3.2" r="2.6" fill="#e0242b"/><path d="M1 12 Q1 6.5 6 6.5 Q11 6.5 11 12Z" fill="#e0242b"/></svg>
      <span class="person-name">Marlo Fenwicke</span>
    </div>
    <p class="person-title">Director</p>
    <p class="address">48 Tarn Lane, Whitianga 3510</p>
    <div class="contact-row row-mobile">
      <svg viewBox="0 0 12 12" aria-hidden="true"><rect x="2.5" y="0.5" width="7" height="11" rx="1.2" fill="none" stroke="#e0242b" stroke-width="1.2"/><circle cx="6" cy="9.6" r=".7" fill="#e0242b"/></svg>
      <span>+ 027 451 9362</span>
    </div>
    <div class="contact-row row-phone">
      <svg viewBox="0 0 12 12" aria-hidden="true"><path d="M0.5 5 Q6 0.5 11.5 5 L10 6.5 L8 5.2 L8 4 Q6 3.3 4 4 L4 5.2 L2 6.5Z" fill="#e0242b"/><rect x="2.5" y="6.5" width="7" height="4.5" rx="1" fill="#e0242b"/></svg>
      <span>+ 07 594 2713</span>
    </div>
    <div class="contact-row row-email">
      <svg viewBox="0 0 12 12" aria-hidden="true"><rect x="0.5" y="2.5" width="11" height="7.5" fill="#e0242b"/><path d="M0.8 2.8 L6 7 L11.2 2.8" fill="none" stroke="#fff" stroke-width="1"/></svg>
      <span>office@keelstoneautomotive.example.nz</span>
    </div>
    <div class="contact-row row-web">
      <svg viewBox="0 0 12 12" aria-hidden="true"><rect x="0.8" y="1.5" width="10.4" height="7.5" fill="none" stroke="#e0242b" stroke-width="1.1"/><circle cx="6" cy="5.2" r="2" fill="none" stroke="#e0242b" stroke-width=".9"/><path d="M4 11 H8" stroke="#e0242b" stroke-width="1.2"/></svg>
      <span>keelstoneautomotive.example.nz</span>
    </div>
  </div>
</section>

<section class="card card--back" aria-label="Business card back">
  <ul class="services">
    <li class="service" style="top:46px;"><svg viewBox="0 0 13 24" aria-hidden="true"><path d="M0 0 L13 12 L0 24Z" fill="#e0242b"/></svg>Vehicle Servicing</li>
    <li class="service" style="top:91px;"><svg viewBox="0 0 13 24" aria-hidden="true"><path d="M0 0 L13 12 L0 24Z" fill="#e0242b"/></svg>All Mechanical Repairs</li>
    <li class="service" style="top:135px;"><svg viewBox="0 0 13 24" aria-hidden="true"><path d="M0 0 L13 12 L0 24Z" fill="#e0242b"/></svg>Warrant of Fitness</li>
    <li class="service" style="top:181px;"><svg viewBox="0 0 13 24" aria-hidden="true"><path d="M0 0 L13 12 L0 24Z" fill="#e0242b"/></svg>Tyres &amp; Wheel Alignments</li>
    <li class="service" style="top:226px;"><svg viewBox="0 0 13 24" aria-hidden="true"><path d="M0 0 L13 12 L0 24Z" fill="#e0242b"/></svg>Automotive Diagnostics</li>
    <li class="service" style="top:271px;"><svg viewBox="0 0 13 24" aria-hidden="true"><path d="M0 0 L13 12 L0 24Z" fill="#e0242b"/></svg>Automotive Parts &amp; Supplies</li>
  </ul>
  <div class="brand-panel">
    <p class="brand-name">Keelstone Prime<br>Automotive</p>
  </div>
  <div class="appointment">
    <span class="appointment-field">Time<span class="blank"></span></span>
    <span class="appointment-field">Date<span class="blank"></span></span>
  </div>
</section>

</body>
</html>
```